Coastline Premier Retreats Business Card Design

Design a business card for Coastline Premier Retreats. Look at the website for colors and reference. Card should have logo, name, title, office number, mobile number, email, URL and a tagline like, "Luxury Hotel & Resort Email Marketing" (This might change).

https://www.coastlinepremierretreats.example

The rest I will leave up to your imagination.

Contact Information for Business Card

Logo, name, title, office number, mobile number, email, URL and a tagline like, "Luxury Hotel & Resort Email Marketing" (This might change).

```html
<!DOCTYPE html>
<html lang="en">
<head>
<meta charset="UTF-8">
<title>Coastline Premier Retreats – Business Card</title>
<link rel="stylesheet" href="https://fonts.googleapis.com/css2?family=Open+Sans:wght@400;600;700&display=swap">
<style>
  :root {
    --stage: #242424;
    --card: #1f1f23;
    --orange: #f47920;
    --white: #ffffff;
    --muted: #e9e9ea;
  }
  * { box-sizing: border-box; margin: 0; padding: 0; }
  html, body {
    width: 1200px; height: 780px; overflow: hidden;
    background: var(--stage);
    font-family: "Open Sans", Arial, sans-serif;
  }
  .stage {
    position: relative; width: 1200px; height: 780px;
    display: flex; align-items: center; justify-content: center; gap: 80px;
  }
  .card {
    position: relative; width: 380px; height: 620px;
    background: var(--card);
    border: 2px solid var(--orange);
    overflow: hidden;
  }
  .card--front { border-radius: 190px 0 190px 0; }
  .card--back  { border-radius: 0 190px 0 190px; }

  /* front: vertical brand name */
  .brand-vertical {
    position: absolute; left: 50%; top: 50%;
    transform: translate(-50%, -50%) rotate(-90deg);
    white-space: nowrap; text-align: center;
    color: var(--white); font-weight: 700;
    font-size: 38px; letter-spacing: 2px; text-transform: uppercase; line-height: 1.15;
  }

  /* back: brand name kept clear of the rounded top-right corner */
  .brand-top {
    position: absolute; top: 64px; left: 36px; width: 260px;
    text-align: center; color: var(--white);
    font-weight: 700; font-size: 19px; line-height: 1.3;
    letter-spacing: 1.5px; text-transform: uppercase;
  }
  .details { position: absolute; left: 56px; right: 24px; top: 300px; }
  .person-name { font-size: 30px; font-weight: 700; line-height: 1.1; color: var(--white); }
  .person-name .first { color: var(--orange); }
  .person-title { margin-top: 4px; font-size: 15px; font-weight: 600; color: var(--white); }
  .tagline { margin-top: 16px; font-size: 15px; color: var(--orange); line-height: 1.35; }
  .contact-list { margin-top: 22px; list-style: none; }
  .contact-list li {
    display: flex; align-items: center; gap: 10px;
    font-size: 13.5px; color: var(--muted); line-height: 1; margin-bottom: 9px;
    white-space: nowrap;
  }
  .contact-list svg { width: 15px; height: 15px; flex: none; fill: none; stroke: var(--orange); stroke-width: 1.8; }
</style>
</head>
<body>
  <main class="stage">
    <section class="card card--front" aria-label="Card front">
      <p class="brand-vertical">Coastline<br>Premier Retreats</p>
    </section>

    <section class="card card--back" aria-label="Card back">
      <p class="brand-top">Coastline<br>Premier Retreats</p>
      <div class="details">
        <h1 class="person-name"><span class="first">Marta</span> Kovalenko</h1>
        <p class="person-title">Co-Founder</p>
        <p class="tagline">Luxury Hotel &amp;<br>Resort Email Marketing</p>
        <ul class="contact-list">
          <li>
            <svg viewBox="0 0 24 24" aria-hidden="true"><path d="M5 3h4l2 5-3 2a12 12 0 0 0 6 6l2-3 5 2v4a2 2 0 0 1-2 2A18 18 0 0 1 3 5a2 2 0 0 1 2-2z"/></svg>
            (555) 014-2758
          </li>
          <li>
            <svg viewBox="0 0 24 24" aria-hidden="true"><rect x="6" y="2" width="12" height="20" rx="2"/><line x1="11" y1="18" x2="13" y2="18"/></svg>
            (555) 017-7777
          </li>
          <li>
            <svg viewBox="0 0 24 24" aria-hidden="true"><circle cx="12" cy="12" r="9"/><path d="M3 12h18M12 3c3 3 3 15 0 18M12 3c-3 3-3 15 0 18"/></svg>
            www.coastlinepremierretreats.example
          </li>
          <li>
            <svg viewBox="0 0 24 24" aria-hidden="true"><rect x="3" y="5" width="18" height="14" rx="1"/><path d="M3 6l9 7 9-7"/></svg>
            info@coastlinepremierretreats.example
          </li>
        </ul>
      </div>
    </section>
  </main>
</body>
</html>
```